Brookvane Consulting Business Card Design

Business Card Design for Brookvane Consulting. Brookvane Consulting is a boutique consultancy based in Atlanta, GA., that specializes in marketing strategy, organization planning, and leadership development. We provide solutions for small businesses and startups as well as Vantage 300 companies.

http://brookvaneconsulting.com/

Target Market(s)

We provide solutions for small businesses and startups as well as Vantage 300 companies.

Industry/Entity Type

Consulting

Contact Information for Business Card

Two sided business card with priority on contact information, logo, tag line (Inspiration to Dream More, Do More, Become More)

Colors

Designer to choose colors to be used in the design.

Requirements
Must have
• contact information, logo, tag line (Inspiration to Dream More, Do More, Become More)
• Simple no over communication.
Nice to have
• I would like to see different placements of logo and creative use of both sides of the card
Should not have
• Do not put too much information on the card.

```html
<!DOCTYPE html>
<html lang="en">
<head>
<meta charset="utf-8">
<title>Brookvane Consulting Business Card</title>
<link href="https://fonts.googleapis.com/css2?family=Lato:wght@400;700&display=swap" rel="stylesheet">
<style>
  :root {
    --backdrop: #e9e7e4;
    --card-dark: #141414;
    --card-mid: #222222;
    --ink-white: #ffffff;
    --ink-grey: #c9c9c9;
    --ink-soft: #9a9a9a;
  }
  * { margin: 0; padding: 0; box-sizing: border-box; }
  html, body {
    width: 1200px;
    height: 769px;
    overflow: hidden;
    background: var(--backdrop);
    font-family: "Lato", sans-serif;
  }
  .sheet {
    position: relative;
    width: 1200px;
    height: 769px;
  }
  .card {
    position: absolute;
    top: 236px;
    width: 525px;
    height: 300px;
    border-radius: 4px;
    overflow: hidden;
    box-shadow: 0 10px 28px rgba(0,0,0,0.25);
  }
  .card--contact { left: 50px; }
  .card--brand { left: 625px; }
  .card-texture {
    position: absolute;
    inset: 0;
    background: linear-gradient(135deg, var(--card-mid) 0%, var(--card-dark) 60%, #0e0e0e 100%);
  }
  .card-content {
    position: absolute;
    inset: 0;
  }
  .wordmark {
    display: flex;
    align-items: center;
    gap: 10px;
    color: var(--ink-white);
    font-weight: 700;
  }
  .wordmark-square {
    width: 14px;
    height: 14px;
    background: var(--ink-white);
  }
  .card--contact .card-content {
    padding: 44px 46px 0 0;
    text-align: right;
  }
  .card--contact .wordmark {
    justify-content: flex-end;
    font-size: 30px;
    line-height: 1.1;
    margin-bottom: 34px;
  }
  .holder-name {
    color: var(--ink-soft);
    font-weight: 700;
    font-size: 17px;
    letter-spacing: 0.5px;
    text-transform: uppercase;
  }
  .holder-title {
    color: var(--ink-grey);
    font-size: 15px;
    margin-top: 3px;
    margin-bottom: 16px;
  }
  .contact-list { list-style: none; }
  .contact-item {
    display: flex;
    justify-content: flex-end;
    align-items: center;
    gap: 8px;
    color: var(--ink-grey);
    font-size: 14px;
    line-height: 22px;
  }
  .contact-icon {
    width: 13px;
    height: 13px;
    fill: none;
    stroke: var(--ink-grey);
    stroke-width: 1.6;
  }
  .card--brand .card-content {
    display: flex;
    flex-direction: column;
    align-items: center;
    justify-content: center;
  }
  .card--brand .wordmark {
    font-size: 40px;
    line-height: 1.1;
    margin-bottom: 30px;
  }
  .card--brand .wordmark-square { width: 18px; height: 18px; }
  .tagline {
    color: var(--ink-grey);
    font-size: 13px;
    letter-spacing: 0.3px;
  }
</style>
</head>
<body>
<main class="sheet">
  <section class="card card--contact">
    <div class="card-texture" role="img" aria-label="Subtle dark tonal grid pattern across the card face"></div>
    <div class="card-content">
      <div class="wordmark"><span class="wordmark-square"></span>Brookvane Consulting</div>
      <p class="holder-name">Darian Whitlock</p>
      <p class="holder-title">Founder/Managing Director</p>
      <ul class="contact-list">
        <li class="contact-item">424-555-0173
          <svg class="contact-icon" viewBox="0 0 16 16"><path d="M3 1.5h3l1.2 3.2-1.8 1.2a8 8 0 0 0 4.7 4.7l1.2-1.8 3.2 1.2v3a1.5 1.5 0 0 1-1.6 1.5A12.5 12.5 0 0 1 1.5 3.1 1.5 1.5 0 0 1 3 1.5z"/></svg>
        </li>
        <li class="contact-item">darian@brookvaneconsulting.com
          <svg class="contact-icon" viewBox="0 0 16 16"><rect x="1.5" y="3.5" width="13" height="9"/><path d="M1.5 3.5 8 9l6.5-5.5"/></svg>
        </li>
        <li class="contact-item">brookvaneconsulting.com
          <svg class="contact-icon" viewBox="0 0 16 16"><circle cx="8" cy="8" r="6.5"/><path d="M1.5 8h13M8 1.5c-2.5 3-2.5 10 0 13M8 1.5c2.5 3 2.5 10 0 13"/></svg>
        </li>
      </ul>
    </div>
  </section>

  <section class="card card--brand">
    <div class="card-texture" role="img" aria-label="Subtle dark tonal grid pattern across the card face"></div>
    <div class="card-content">
      <div class="wordmark"><span class="wordmark-square"></span>Brookvane Consulting</div>
      <p class="tagline">Inspiration to Dream More, Do More, Become More</p>
    </div>
  </section>
</main>
</body>
</html>
```